Business Card Design Project

We are rebranding an existing automotive collision repair business. The business is called dent haven. I have attached logo but I'm not tied to that. I want to leave this wide open.

I want this card to say we are professional, competent, cutting edge. We are focused on customers and use a lot of the latest technology to make the customer experience different. We sign customers in on iPads. Paperwork I signed electronically and updates are sent via text, email, logging on a website or as they wish. I want this innovation and image to come through in our cards

Target Market(s)

60%. Women 40% men. Age 35-60

Industry/Entity Type

Automotive

Requirements
Must have
• The card must have name, title, phone,email, cell, web page

```html
<!DOCTYPE html>
<html lang="en">
<head>
<meta charset="utf-8">
<title>Dent Haven – Business Card</title>
<link rel="stylesheet" href="https://fonts.googleapis.com/css2?family=Source+Sans+3:wght@400;600;700&display=swap">
<style>
  :root {
    --page: #e9e4dc;
    --card-dark: #3a3a3a;
    --card-light: #f4f4f4;
    --accent: #7dc242;
    --accent-deep: #5a9a2a;
    --ink-light: #ffffff;
    --ink-muted: #e2e2e2;
    --shadow: rgba(0, 0, 0, 0.28);
  }
  * { box-sizing: border-box; margin: 0; padding: 0; }
  html, body {
    width: 1200px; height: 864px; overflow: hidden;
    background: var(--page);
    font-family: "Source Sans 3", "Helvetica Neue", Arial, sans-serif;
  }
  .canvas { position: relative; width: 1200px; height: 864px; }

  .card {
    position: absolute;
    width: 560px; height: 320px;
    border-radius: 4px;
    overflow: hidden;
    background: var(--card-dark);
    box-shadow: 0 14px 30px var(--shadow), 0 2px 6px var(--shadow);
  }
  .card--front { left: 150px; top: 100px; }
  .card--back  { left: 490px; top: 444px; }

  .front-bands { position: absolute; inset: 0; width: 100%; height: 100%; }
  .brand-name {
    position: absolute;
    color: var(--accent);
    font-weight: 700;
    letter-spacing: 0.5px;
    line-height: 1;
    white-space: nowrap;
  }
  .card--front .brand-name { right: 34px; top: 28px; font-size: 30px; color: var(--accent-deep); }

  .holder { position: absolute; left: 42px; top: 180px; }
  .holder-name { color: var(--ink-light); font-size: 21px; font-weight: 600; }
  .holder-title { color: var(--accent); font-size: 17px; font-weight: 400; margin-top: 2px; }

  .contacts {
    position: absolute; left: 318px; top: 146px;
    list-style: none;
    color: var(--ink-muted);
    font-size: 15px;
    line-height: 22px;
  }
  .contacts li { display: flex; align-items: center; gap: 8px; white-space: nowrap; }
  .contacts svg { width: 12px; height: 12px; flex: none; }

  .card--back .brand-name {
    left: 0; right: 0; top: 112px;
    text-align: center;
    font-size: 56px;
  }
  .back-rule {
    position: absolute; left: 110px; right: 110px; top: 184px;
    height: 2px; background: var(--accent); opacity: 0.55;
  }
  .back-web {
    position: absolute; left: 0; right: 0; top: 218px;
    text-align: center;
    color: var(--accent);
    font-size: 17px;
  }
</style>
</head>
<body>
<main class="canvas">

  <section class="card card--front" aria-label="Business card front">
    <svg class="front-bands" viewBox="0 0 560 320" preserveAspectRatio="none" aria-hidden="true">
      <path d="M0 0 H560 V88 C440 96 360 58 250 52 C150 46 70 80 0 84 Z" fill="var(--card-light)"/>
      <path d="M0 84 C70 80 150 46 250 52 C360 58 440 96 560 88" fill="none" stroke="var(--accent)" stroke-width="4"/>
      <path d="M0 92 C80 86 160 56 255 60 C365 66 440 100 560 96" fill="none" stroke="#9a9a9a" stroke-width="1.2"/>
    </svg>

    <div class="brand-name">Dent Haven</div>

    <div class="holder">
      <p class="holder-name">Owen Mercer</p>
      <p class="holder-title">Managing Director</p>
    </div>

    <ul class="contacts">
      <li>
        <svg viewBox="0 0 12 12" aria-hidden="true"><path d="M3 1 L5 3.5 L4 5 C4.8 6.6 5.6 7.4 7 8 L8.5 7 L11 9 L9.5 11 C5 10.5 1.5 7 1 2.5 Z" fill="var(--accent)"/></svg>
        555.0142.7730
      </li>
      <li>
        <svg viewBox="0 0 12 12" aria-hidden="true"><rect x="3" y="0.5" width="6" height="11" rx="1.2" fill="var(--accent)"/><rect x="4" y="2" width="4" height="6" fill="var(--card-dark)"/></svg>
        555.0178.3361
      </li>
      <li>
        <svg viewBox="0 0 12 12" aria-hidden="true"><rect x="1" y="4" width="10" height="6" rx="1" fill="var(--accent)"/><rect x="3" y="1" width="6" height="3" fill="var(--accent)"/></svg>
        555.0195.4402
      </li>
      <li>
        <svg viewBox="0 0 12 12" aria-hidden="true"><rect x="0.5" y="2" width="11" height="8" rx="1" fill="var(--accent)"/><path d="M1 2.5 L6 6.5 L11 2.5" fill="none" stroke="var(--card-dark)" stroke-width="1"/></svg>
        info@denthaven.com
      </li>
      <li>
        <svg viewBox="0 0 12 12" aria-hidden="true"><circle cx="6" cy="6" r="5.5" fill="var(--accent)"/><path d="M0.5 6 H11.5 M6 0.5 C3 3 3 9 6 11.5 M6 0.5 C9 3 9 9 6 11.5" fill="none" stroke="var(--card-dark)" stroke-width="0.8"/></svg>
        www.denthaven.com
      </li>
    </ul>
  </section>

  <section class="card card--back" aria-label="Business card back">
    <div class="brand-name">Dent Haven</div>
    <div class="back-rule"></div>
    <p class="back-web">www.denthaven.com</p>
  </section>

</main>
</body>
</html>
```